Pet Sitting Business Card

Would like a business card designed for my new pet sitting business
Card needs to match with logo design.
Blue and Orange are the theme colours.

Simple yet sophisticated design

company name:- MEADOWLARK PET CARE
Dana Kovich
Owner
0452716093
dana@meadowlarkpetcare.com.au
www.meadowlarkpetcare.com.au

I'm going to close my deadline early. I will be picking a winner by the 10th of May. Please submit designs before then.
thank you

Target Market(s)

All types of professional pet lovers wishing to have their pet looked after

Industry/Entity Type

Pet

Requirements
Must have
• Logo design
Blue and orange

```html
<!DOCTYPE html>
<html lang="en">
<head>
<meta charset="utf-8">
<title>Meadowlark Pet Care – Business Card</title>
<link href="https://fonts.googleapis.com/css2?family=Exo+2:wght@400;600;700&display=swap" rel="stylesheet">
<style>
  :root {
    --page-bg: #e9ecef;
    --card-white: #ffffff;
    --brand-blue: #2a8be6;
    --brand-cyan: #5ed3df;
    --brand-orange: #f28a26;
    --ink-white: #ffffff;
    --card-shadow: rgba(20, 40, 70, 0.18);
  }
  * { margin: 0; padding: 0; box-sizing: border-box; }
  html, body {
    width: 1200px;
    height: 720px;
    overflow: hidden;
    background: var(--page-bg);
    font-family: "Exo 2", Arial, sans-serif;
  }
  .canvas {
    position: relative;
    width: 1200px;
    height: 720px;
  }
  .card {
    position: absolute;
    top: 205px;
    width: 540px;
    height: 310px;
    border-radius: 22px;
    overflow: hidden;
    background: var(--card-white);
    box-shadow: 0 10px 30px var(--card-shadow);
  }
  .card--front { left: 40px; }
  .card--back { left: 620px; }
  .card__art {
    position: absolute;
    inset: 0;
    width: 100%;
    height: 100%;
  }
  .brand-name {
    position: absolute;
    text-align: center;
    color: var(--brand-blue);
    font-weight: 700;
    line-height: 1.05;
    letter-spacing: 0.04em;
  }
  .brand-name__main { display: block; }
  .brand-name__sub { display: block; letter-spacing: 0.2em; }
  .card--front .brand-name {
    left: 0; right: 0;
    top: 140px;
    font-size: 34px;
  }
  .card--front .brand-name__sub { font-size: 22px; }
  .card--back .brand-name {
    left: 170px; right: 40px;
    top: 212px;
    font-size: 28px;
  }
  .card--back .brand-name__sub { font-size: 18px; }
  .holder {
    position: absolute;
    top: 30px;
    right: 26px;
    text-align: right;
    color: var(--ink-white);
    text-transform: uppercase;
  }
  .holder__name { font-size: 17px; font-weight: 600; letter-spacing: 0.05em; }
  .holder__role { font-size: 11px; font-weight: 400; letter-spacing: 0.08em; margin-top: 2px; }
  .contact-list {
    position: absolute;
    left: 20px;
    top: 76px;
    list-style: none;
    color: var(--ink-white);
    font-size: 11px;
  }
  .contact-list__item {
    display: flex;
    align-items: center;
    gap: 7px;
    height: 18px;
    white-space: nowrap;
  }
  .contact-list__icon {
    width: 13px;
    height: 13px;
    flex: none;
  }
</style>
</head>
<body>
<main class="canvas">

  <section class="card card--front" aria-label="Business card front">
    <svg class="card__art" viewBox="0 0 540 310" aria-hidden="true">
      <defs>
        <linearGradient id="front-sweep" x1="0" y1="0" x2="1" y2="0">
          <stop offset="0" stop-color="var(--brand-blue)"/>
          <stop offset="0.45" stop-color="var(--brand-cyan)"/>
          <stop offset="1" stop-color="var(--brand-blue)"/>
        </linearGradient>
      </defs>
      <path d="M0,0 H540 V32 C380,22 170,55 0,140 Z" fill="url(#front-sweep)"/>
    </svg>
    <div class="brand-name">
      <span class="brand-name__main">MEADOWLARK</span>
      <span class="brand-name__sub">PET CARE</span>
    </div>
  </section>

  <section class="card card--back" aria-label="Business card back">
    <svg class="card__art" viewBox="0 0 540 310" aria-hidden="true">
      <defs>
        <linearGradient id="back-band" x1="0" y1="0" x2="1" y2="0">
          <stop offset="0" stop-color="var(--brand-blue)"/>
          <stop offset="0.45" stop-color="var(--brand-cyan)"/>
          <stop offset="1" stop-color="var(--brand-blue)"/>
        </linearGradient>
      </defs>
      <path d="M0,0 H540 V100 C420,110 230,150 0,285 Z" fill="url(#back-band)"/>
      <path d="M0,294 C230,159 420,118 540,108" fill="none" stroke="var(--brand-orange)" stroke-width="4"/>
    </svg>

    <div class="holder">
      <div class="holder__name">Theo Marsh</div>
      <div class="holder__role">Financial Advisor</div>
    </div>

    <ul class="contact-list">
      <li class="contact-list__item">
        <svg class="contact-list__icon" viewBox="0 0 14 14" aria-hidden="true"><circle cx="7" cy="7" r="7" fill="#fff"/><path d="M4.6,3.6 l1.3,-0.3 0.7,1.8 -0.8,0.6 c0.4,0.9 1,1.5 1.9,1.9 l0.6,-0.8 1.8,0.7 -0.3,1.3 c-3,0 -5.2,-2.2 -5.2,-5.2z" fill="var(--brand-blue)"/></svg>
        <span>013 579 2468</span>
      </li>
      <li class="contact-list__item">
        <svg class="contact-list__icon" viewBox="0 0 14 14" aria-hidden="true"><circle cx="7" cy="7" r="7" fill="#fff"/><rect x="4.8" y="3" width="4.4" height="8" rx="0.8" fill="var(--brand-blue)"/></svg>
        <span>013 579 2468</span>
      </li>
      <li class="contact-list__item">
        <svg class="contact-list__icon" viewBox="0 0 14 14" aria-hidden="true"><circle cx="7" cy="7" r="7" fill="#fff"/><rect x="3.5" y="4.5" width="7" height="5" fill="var(--brand-blue)"/><path d="M3.5,4.5 L7,7.3 10.5,4.5" fill="none" stroke="#fff" stroke-width="0.8"/></svg>
        <span>hello@theomarsh.net</span>
      </li>
      <li class="contact-list__item">
        <svg class="contact-list__icon" viewBox="0 0 14 14" aria-hidden="true"><circle cx="7" cy="7" r="7" fill="#fff"/><circle cx="7" cy="7" r="3.6" fill="none" stroke="var(--brand-blue)" stroke-width="1"/><path d="M3.4,7 H10.6 M7,3.4 C5.3,5.5 5.3,8.5 7,10.6 M7,3.4 C8.7,5.5 8.7,8.5 7,10.6" fill="none" stroke="var(--brand-blue)" stroke-width="0.8"/></svg>
        <span>www.theomarsh.net</span>
      </li>
      <li class="contact-list__item">
        <svg class="contact-list__icon" viewBox="0 0 14 14" aria-hidden="true"><circle cx="7" cy="7" r="7" fill="#fff"/><path d="M7,11 C5,8.6 4.4,7.4 4.4,6 a2.6,2.6 0 0 1 5.2,0 c0,1.4 -0.6,2.6 -2.6,5z" fill="var(--brand-blue)"/><circle cx="7" cy="6" r="1" fill="#fff"/></svg>
        <span>47, 5th Floor, Harbour Lane NTH</span>
      </li>
    </ul>

    <div class="brand-name">
      <span class="brand-name__main">MEADOWLARK</span>
      <span class="brand-name__sub">PET CARE</span>
    </div>
  </section>

</main>
</body>
</html>
```